Lumra Learning Web Design Project

Who We are:
Lumra Learning is education information portal/ magazine, providing information about the Chinese and International education markets. Our aim is to help school principals improve there curriculum, and parents in understanding this curriculum.

Project Brief:
The site will include education news updates, educational services, curriculum developments and overseas study. We hope the site represents the cross cultural bridge between the west and east. The site will cover both the Sciences and Arts.

Note:
The logo design competition is also underway so we only need the website design

What We want:
This competition is for Design only no coding!
Design a home page based on Template 1,2 or 3. I only need to select one.
The design of an article page.

Optional
Design a Parvex Shutters metro style splash page.

Sites We like:
http://www.qv.com.cn/tonguebridge/default.aspx
http://www.dailyuniversitybulletin.co.uk/
http://kptz.sinocraftlearn.net/

Template Explanations:
Template 1-
The main information has a dynamic sliding category view that when clicked displays the relevant info.
In addition to the main upper menu it also has a left hand sliding menu that pops out on click or gesture

Template 2-
Has limited number of Articles most of the menus are drop downs from the top menu

Template 3-
No Top menu

Target Market(s)

Teachers, principals and parents

Industry/Entity Type

Education

Requirements
Should not have
• kindergarten preschool feel

```html
<!DOCTYPE html>
<html lang="en">
<head>
<meta charset="utf-8">
<title>Lumra Learning — Home</title>
<link href="https://fonts.googleapis.com/css2?family=Montserrat:wght@300;400;600;700&display=swap" rel="stylesheet">
<style>
:root{
  --blue:#1f5796;
  --blue-dark:#174a86;
  --sky:#2f93c6;
  --orange:#ec8a1c;
  --green:#3a9c3c;
  --lime:#8cc63f;
  --red:#d9403f;
  --crimson:#b73232;
  --purple:#5d3a8f;
  --pink:#e02a7b;
  --yellow:#f2c400;
  --navtext:#c8262d;
  --text:#6b6b6b;
  --white:#ffffff;
  --page:#e9e9e9;
}
*{box-sizing:border-box;margin:0;padding:0}
html,body{width:1200px;height:1066px;overflow:hidden}
body{
  position:relative;
  font-family:"Montserrat",Arial,sans-serif;
  background:radial-gradient(ellipse at 50% 35%,#f7f7f7 0%,#e6e6e6 55%,#d9d9d9 100%);
  color:var(--text);
}
.abs{position:absolute}

/* header */
.brand{left:197px;top:58px;display:flex;align-items:center;gap:8px}
.brand-dot{width:22px;height:22px;border-radius:50%;background:var(--red)}
.brand-name{font-size:16px;font-weight:700;color:var(--blue);letter-spacing:.2px}
.search{left:790px;top:78px;width:206px;height:28px;background:var(--white);border:1px solid #cfcfcf;
  font-size:11px;color:#a0a0a0;padding:7px 0 0 10px}
.search svg{position:absolute;right:6px;top:5px}

/* top nav */
.topnav{left:195px;top:116px;width:801px;height:38px;background:var(--white);display:flex}
.topnav a{height:38px;display:flex;align-items:center;justify-content:center;text-decoration:none;
  font-size:12px;color:var(--navtext);border-bottom:3px solid;border-right:1px solid #e3e3e3}
.topnav a.current{background:var(--blue);color:var(--white);border-bottom-color:var(--blue)}
.topnav .fill{flex:1;border-bottom:3px solid var(--yellow)}

/* side menu */
.sidemenu{left:195px;top:164px;width:60px}
.sidemenu a,.social span{display:flex;flex-direction:column;align-items:center;justify-content:center;
  width:60px;text-decoration:none;color:var(--white);font-size:8.5px;font-weight:700;gap:7px}
.sidemenu a{height:72px}
.social{left:195px;top:679px;width:60px}
.social span{height:59.8px}
.social i{display:block;width:18px;height:18px;border-radius:50%;background:rgba(255,255,255,.9)}

/* hero */
.hero{left:263px;top:164px;width:537px;height:236px;display:flex}
.hero-text{width:243px;background:linear-gradient(180deg,#2a63a3,#1b4f8f);padding:49px 0 0 14px;color:var(--white)}
.hero-text h1{font-size:20px;font-weight:300;line-height:17.6px;letter-spacing:-.2px}
.hero-text p{font-size:9.5px;line-height:13.5px;margin-top:9px;color:#dfe8f3;width:220px}
.more{display:flex;align-items:center;gap:5px;font-size:13px;font-weight:300;color:var(--white);margin-top:12px}
.hero-photo{flex:1;background:linear-gradient(90deg,#5a5d5c 0%,#7a7d7b 40%,#cfcfcf 70%,#e6e6e6 100%)}

/* categories */
.section-head{color:var(--white);font-size:22px;font-weight:300;display:flex;align-items:center}
.cat-head{left:263px;top:409px;width:537px;height:44px;background:linear-gradient(180deg,#2a63a3,#174a86);padding-left:14px}
.cat-panel{left:263px;top:453px;width:537px;height:195px;background:var(--white)}
.teaser{width:256px;height:86px;display:flex;padding:8px;gap:10px;color:var(--white)}
.teaser .thumb{width:96px;height:70px;flex:none}
.teaser h3{font-size:10.5px;font-weight:700;line-height:13.6px;margin-top:7px}
.teaser .more{font-size:13px;margin-top:6px}
.teaser.blue{left:271px;top:462px;background:var(--blue)}
.teaser.red{left:271px;top:557px;background:var(--red)}
.feature{left:536px;top:462px;width:256px;height:180px;background:var(--green);padding:7px;color:var(--white)}
.feature .photo{height:136px;background:linear-gradient(135deg,#c9a27a,#e8c99a 45%,#b8d2df 80%)}
.feature h3{font-size:10.5px;font-weight:700;line-height:13.6px;margin-top:7px}

.tags{top:652px;width:264px}
.tags span{display:flex;align-items:center;height:44px;padding-left:11px;font-size:21px;font-weight:300;color:var(--white)}
.tags.left{left:263px}
.tags.right{left:536px}

/* right column */
.listbox{left:808px;width:188px;background:var(--white)}
.listbox h2{height:44px;padding-left:11px}
.listbox li{list-style:none;height:49px;border-left:3px solid;border-bottom:1px solid #e8e8e8;
  padding:9px 8px 0 7px;font-size:10.5px;font-weight:300;line-height:15.4px;color:var(--text)}
.articles{top:164px}
.articles h2{background:var(--orange)}
.posts{top:513px;height:315px;overflow:hidden}
.posts h2{background:var(--sky)}

/* footer */
.footlinks{left:263px;top:836px;width:733px;height:145px;background:var(--white);display:flex}
.footlinks section{border-bottom:4px solid;border-right:1px solid #e6e6e6;padding:21px 0 0 40px}
.footlinks h4{font-size:14px;font-weight:700;margin-bottom:5px}
.footlinks li{list-style:none;font-size:10px;line-height:15.6px;color:#666}
.copyright{left:263px;top:990px;width:733px;height:48px;background:linear-gradient(180deg,#2a63a3,#174a86);
  color:var(--white);font-size:10.5px;display:flex;align-items:center;justify-content:center}
.copyright em{font-style:normal;color:#b8c9de;margin-left:4px}
</style>
</head>
<body>

<header>
  <div class="abs brand"><span class="brand-dot"></span><span class="brand-name">LUMRA LEARNING</span></div>
  <div class="abs search">SEARCH
    <svg width="18" height="18" viewBox="0 0 18 18"><circle cx="7.5" cy="7.5" r="5.5" fill="none" stroke="#9a9a9a" stroke-width="2"/><line x1="11.5" y1="11.5" x2="16" y2="16" stroke="#9a9a9a" stroke-width="2.6" stroke-linecap="round"/></svg>
  </div>
  <nav class="abs topnav">
    <a class="current" style="width:71px">HOME</a>
    <a style="width:96px;border-bottom-color:var(--orange)">ABOUT US</a>
    <a style="width:128px;border-bottom-color:var(--green)">FOR STUDENTS</a>
    <a style="width:83px;border-bottom-color:var(--crimson)">LESSON</a>
    <a style="width:67px;border-bottom-color:var(--purple)">BLOG</a>
    <a style="width:82px;border-bottom-color:var(--sky)">JOIN US</a>
    <a style="width:95px;border-bottom-color:var(--green)">CONTACT</a>
    <span class="fill"></span>
  </nav>
</header>

<nav class="abs sidemenu">
  <a style="background:var(--blue)"><svg width="22" height="22" viewBox="0 0 22 22"><path d="M11 2 1 11h3v9h5v-6h4v6h5v-9h3z" fill="#fff"/></svg>HOME</a>
  <a style="background:var(--orange)"><svg width="24" height="24" viewBox="0 0 24 24"><circle cx="12" cy="12" r="11" fill="#fff"/><rect x="10.6" y="10" width="2.8" height="8" fill="var(--orange)"/><circle cx="12" cy="6.8" r="1.7" fill="var(--orange)"/></svg>ABOUT US</a>
  <a style="background:var(--green)"><svg width="30" height="22" viewBox="0 0 30 22"><path d="M15 2 1 8l14 6 14-6z" fill="#fff"/><path d="M7 11v6c4 3 12 3 16 0v-6l-8 3.5z" fill="#fff"/><line x1="3" y1="9" x2="3" y2="16" stroke="#fff" stroke-width="1.5"/></svg>STUDENTS</a>
  <a style="background:var(--crimson)"><svg width="26" height="20" viewBox="0 0 26 20"><path d="M2 2h9c1 0 2 1 2 2v14c0-1-1-2-2-2H2zM24 2h-9c-1 0-2 1-2 2v14c0-1 1-2 2-2h9z" fill="#fff"/><g stroke="var(--crimson)" stroke-width="1"><line x1="4" y1="6" x2="10" y2="6"/><line x1="4" y1="9" x2="10" y2="9"/><line x1="4" y1="12" x2="10" y2="12"/><line x1="16" y1="6" x2="22" y2="6"/><line x1="16" y1="9" x2="22" y2="9"/><line x1="16" y1="12" x2="22" y2="12"/></g></svg>LESSON</a>
  <a style="background:var(--purple)"><svg width="18" height="22" viewBox="0 0 18 22"><path d="M2 1h10l5 5v15H2z" fill="none" stroke="#fff" stroke-width="1.6"/><g stroke="#fff" stroke-width="1.4"><line x1="5" y1="9" x2="14" y2="9"/><line x1="5" y1="12" x2="14" y2="12"/><line x1="5" y1="15" x2="14" y2="15"/></g></svg>BLOG</a>
  <a style="background:var(--sky)"><svg width="20" height="20" viewBox="0 0 20 20"><g fill="none" stroke="#fff" stroke-width="2"><rect x="2" y="9" width="7" height="10" rx="3.5" transform="rotate(45 5.5 14)"/><rect x="11" y="1" width="7" height="10" rx="3.5" transform="rotate(45 14.5 6)"/></g></svg>JOIN US</a>
  <a style="background:var(--green)"><svg width="24" height="17" viewBox="0 0 24 17"><rect x="1" y="1" width="22" height="15" fill="none" stroke="#fff" stroke-width="1.6"/><path d="M1 1l11 9 11-9M1 16l8-7M23 16l-8-7" fill="none" stroke="#fff" stroke-width="1.4"/></svg>CONTACT</a>
</nav>

<div class="abs social" aria-label="Social links">
  <span style="background:#2c4f98"><i></i></span>
  <span style="background:#2cb7e3"><i></i></span>
  <span style="background:var(--red)"><i></i></span>
  <span style="background:#1b84bf"><i></i></span>
  <span style="background:var(--crimson)"><i></i></span>
  <span style="background:var(--orange)"><svg width="22" height="22" viewBox="0 0 22 22"><circle cx="4" cy="18" r="3" fill="#fff"/><path d="M1 9a12 12 0 0 1 12 12M1 2a19 19 0 0 1 19 19" fill="none" stroke="#fff" stroke-width="3.4"/></svg></span>
</div>

<main>
  <section class="abs hero">
    <div class="hero-text">
      <h1>RAISING THE SKILL LEVELS OF STUDENTS IN HOME CONVENIENCE</h1>
      <p>Lorem ipsum dolor sit amet, consectetuer adipiscing elit, sed diam nonummy nibh euismod tincidunt ut.</p>
      <div class="more"><svg width="16" height="12" viewBox="0 0 16 12"><path d="M1 1l5 5-5 5M8 1l5 5-5 5" fill="none" stroke="#fff" stroke-width="2.2"/></svg>read more</div>
    </div>
    <div class="hero-photo" role="img" aria-label="Photo of a smiling teacher in a white coat in front of a chalkboard with formulas"></div>
  </section>

  <h2 class="abs section-head cat-head">CATEGORIES</h2>
  <div class="abs cat-panel"></div>
  <article class="abs teaser blue">
    <div class="thumb" role="img" aria-label="Photo of pupils raising hands in a classroom" style="background:linear-gradient(135deg,#2e3d4a,#4d6170 60%,#7a6e62)"></div>
    <div><h3>Lorem ipsum dolor sit amet, consectetuer adipiscing elit.</h3>
      <div class="more"><svg width="16" height="12" viewBox="0 0 16 12"><path d="M1 1l5 5-5 5M8 1l5 5-5 5" fill="none" stroke="#fff" stroke-width="2.2"/></svg>read more</div></div>
  </article>
  <article class="abs teaser red">
    <div class="thumb" role="img" aria-label="Photo of a student studying at a computer lab" style="background:linear-gradient(135deg,#d8dde0,#b9c3b0 50%,#6fa14a)"></div>
    <div><h3>Lorem ipsum dolor sit amet, consectetuer adipiscing elit.</h3>
      <div class="more"><svg width="16" height="12" viewBox="0 0 16 12"><path d="M1 1l5 5-5 5M8 1l5 5-5 5" fill="none" stroke="#fff" stroke-width="2.2"/></svg>read more</div></div>
  </article>
  <article class="abs feature">
    <div class="photo" role="img" aria-label="Photo of a teacher helping children draw at a classroom desk"></div>
    <h3>Lorem ipsum dolor sit amet, consectetuer adipiscing elit.</h3>
  </article>

  <div class="abs tags left">
    <span style="background:var(--red)">EUROPE</span>
    <span style="background:var(--sky)">ASIA</span>
    <span style="background:var(--orange)">USA</span>
    <span style="background:var(--green)">AUSTRALIA</span>
  </div>
  <div class="abs tags right">
    <span style="background:var(--orange)">DRAMA</span>
    <span style="background:var(--green)">SCIENCE</span>
    <span style="background:var(--sky)">ENGLISH</span>
    <span style="background:var(--red)">ARTS</span>
  </div>
</main>

<aside>
  <section class="abs listbox articles">
    <h2 class="section-head">ARTICLES</h2>
    <ul>
      <li style="border-color:var(--lime)">Ut viverra nibh sit amet eros luctus convallis.</li>
      <li style="border-color:var(--green)">Phasellus et libero at leo molestie dapibus.</li>
      <li style="border-color:var(--sky)">Ut viverra nibh sit amet eros luctus convallis.</li>
      <li style="border-color:var(--purple)">Suspendisse dignissim sapien hendrerit mi</li>
      <li style="border-color:var(--orange)">Pellentesque, convallis tincidunt justo auctor.</li>
      <li style="border-color:var(--red)">Proin ut ligula egestas, tempus dui vel, sollicitudin leo.</li>
    </ul>
  </section>
  <section class="abs listbox posts">
    <h2 class="section-head">BLOG POSTS</h2>
    <ul>
      <li style="border-color:var(--sky)">Ut viverra nibh sit amet eros luctus convallis.</li>
      <li style="border-color:var(--green)">Phasellus et libero at leo molestie dapibus.</li>
      <li style="border-color:var(--sky)">Ut viverra nibh sit amet eros luctus convallis.</li>
      <li style="border-color:var(--blue)">Suspendisse dignissim sapien hendrerit mi</li>
      <li style="border-color:var(--lime)">Pellentesque, convallis tincidunt justo auctor.</li>
      <li style="border-color:var(--orange)">Proin ut ligula egestas, tempus dui vel, sollicitudin leo.</li>
    </ul>
  </section>
</aside>

<footer>
  <div class="abs footlinks">
    <section style="width:178px;border-bottom-color:var(--sky)"><h4 style="color:var(--sky)">Quick Links</h4>
      <ul><li>Home</li><li>About Us</li><li>Support</li><li>Team</li><li>Contact Us</li></ul></section>
    <section style="width:186px;border-bottom-color:var(--orange)"><h4 style="color:var(--orange)">Education</h4>
      <ul><li>Syllabus</li><li>Submit a Content</li><li>Consulting</li><li>Programs</li></ul></section>
    <section style="width:180px;border-bottom-color:var(--pink)"><h4 style="color:var(--pink)">Quick Links</h4>
      <ul><li>Home</li><li>About Us</li><li>Support</li><li>Team</li><li>Contact Us</li></ul></section>
    <section style="flex:1;border-right:0;border-bottom-color:var(--lime)"><h4 style="color:var(--lime)">Education</h4>
      <ul><li>Syllabus</li><li>Submit a Content</li><li>Consulting</li><li>Programs</li></ul></section>
  </div>
  <div class="abs copyright">Copyright © 2013 LumraLearning.<em>All rights reserved</em></div>
</footer>

</body>
</html>
```